Need CATCHY/VIVID Banner design for my new UTV/ATV/Off Road Vehicle turn signal/lighting company

I need a banner ad designed so I can advertise on several different ATV (all terrain vehicle), UTV (Utility Vehicles), Golf Cart and Off-Road Vehicle forums. Ads need to be very catchy and produce a call to action. Action is getting hits to my website. Our main business is selling turn signal kits to make your side by side or your ATV/UTV street legal, as some states now allow you to drive these on public roads if you have the following items: Turn Signals, Horn, Lighted license plate bracket, headlights and brake lights. We sell all of these items for just about any model vehicle out there. Our call to action for this banner would be to get more website visits.

Target Market(s)

Off-road/outdoor enthusiasts,

Industry/Entity Type

Car Accessorie

Font styles to use
Sans Serif

Requirements
Must have
• Ad size need to be either 728x90 or 300x250. Colorful ad with an off-road vehicle integrated to the design (think UTV, side-by-side, etc.
Nice to have
• Nice to haves would be anything that makes this banner ad stand out on very boring web pages.
Should not have
• anything dull

```html
<!DOCTYPE html>
<html lang="en">
<head>
<meta charset="UTF-8">
<title>TrailBlink – ATV &amp; UTV Signal Kits Banner</title>
<link rel="stylesheet" href="https://fonts.googleapis.com/css2?family=Montserrat:wght@700;800;900&display=swap">
<style>
  :root {
    --bg-dark: #1c0508;
    --bg-mid: #7a0a12;
    --bg-red: #d8121c;
    --bg-bright: #ee1c25;
    --accent-yellow: #fcb813;
    --accent-orange: #f39a12;
    --text-white: #ffffff;
    --text-yellow: #fcc514;
    --vehicle-grey: #8a8a86;
    --vehicle-dark: #2b2b2b;
  }
  * { margin: 0; padding: 0; box-sizing: border-box; }
  html, body {
    width: 1200px;
    height: 148px;
    overflow: hidden;
    background: #ffffff;
  }
  .banner {
    position: relative;
    width: 1200px;
    height: 148px;
    overflow: hidden;
    font-family: "Montserrat", Arial, sans-serif;
    background:
      radial-gradient(ellipse 320px 120px at 560px 60px, rgba(255,120,120,0.25), transparent 70%),
      linear-gradient(90deg, var(--bg-dark) 0%, var(--bg-mid) 22%, var(--bg-red) 45%, var(--bg-bright) 70%, var(--bg-red) 100%);
  }
  .banner__shapes {
    position: absolute;
    inset: 0;
  }
  .brand {
    position: absolute;
    left: 12px;
    top: 10px;
    width: 250px;
    text-align: center;
    color: var(--text-white);
  }
  .brand__name {
    display: flex;
    align-items: center;
    justify-content: center;
    gap: 8px;
    height: 80px;
    font-size: 30px;
    font-weight: 800;
    letter-spacing: 0.5px;
  }
  .brand__dot {
    width: 14px;
    height: 14px;
    border-radius: 50%;
    background: var(--accent-yellow);
  }
  .brand__tagline {
    font-weight: 800;
    line-height: 1;
    text-transform: uppercase;
  }
  .brand__tagline-main {
    display: block;
    font-size: 20.5px;
    letter-spacing: -0.2px;
  }
  .brand__tagline-sub {
    display: block;
    margin-top: 4px;
    font-size: 13px;
    letter-spacing: 0.1px;
  }
  .vehicle {
    position: absolute;
    border-radius: 18px;
  }
  .vehicle--sport {
    left: 272px;
    top: 22px;
    width: 196px;
    height: 122px;
    background: radial-gradient(ellipse at 50% 55%, var(--vehicle-grey) 0%, #5c5a58 55%, rgba(60,20,20,0) 80%);
  }
  .vehicle--utility {
    left: 900px;
    top: 4px;
    width: 236px;
    height: 140px;
    background: radial-gradient(ellipse at 50% 55%, #3a3a3a 0%, var(--vehicle-dark) 55%, rgba(40,40,40,0) 82%);
  }
  .headline {
    position: absolute;
    left: 450px;
    top: 22px;
    width: 400px;
    text-align: center;
    color: var(--text-white);
  }
  .headline__title {
    font-size: 33px;
    font-weight: 800;
    line-height: 1;
    letter-spacing: 0.3px;
  }
  .headline__subtitle {
    margin-top: 9px;
    font-size: 17.5px;
    font-weight: 800;
    color: var(--text-yellow);
    letter-spacing: 0.4px;
  }
  .features {
    display: flex;
    justify-content: center;
    align-items: center;
    gap: 22px;
    margin-top: 13px;
    list-style: none;
  }
  .features__icon {
    display: block;
    height: 28px;
  }
</style>
</head>
<body>
  <div class="banner">
    <svg class="banner__shapes" width="1200" height="148" viewBox="0 0 1200 148" aria-hidden="true">
      <polygon points="828,88 922,0 1200,0 1200,148 900,148" fill="var(--accent-yellow)"/>
      <polygon points="1110,148 1200,62 1200,148" fill="var(--accent-orange)"/>
      <polygon points="1150,148 1200,100 1200,148" fill="var(--bg-red)"/>
    </svg>

    <div class="brand">
      <div class="brand__name"><span class="brand__dot"></span>TrailBlink</div>
      <p class="brand__tagline">
        <span class="brand__tagline-main">Turn Signal Kits</span>
        <span class="brand__tagline-sub">&amp; Lighting Accessories</span>
      </p>
    </div>

    <div class="vehicle vehicle--sport" role="img" aria-label="Sport side-by-side off-road vehicle in grey and orange"></div>

    <div class="headline">
      <h1 class="headline__title">ATV &amp; UTV VECHICLE</h1>
      <p class="headline__subtitle">SIGNAL KITS AND LIGHTING</p>
      <ul class="features">
        <li aria-label="Brake lights">
          <svg class="features__icon" width="30" height="28" viewBox="0 0 30 28" fill="none" stroke="#fff" stroke-width="2.4" stroke-linecap="round">
            <circle cx="15" cy="14" r="9" fill="#fff" stroke="none"/>
            <path d="M5 4 A14 14 0 0 0 5 24 M25 4 A14 14 0 0 1 25 24"/>
            <path d="M15 8 V15" stroke="#d8121c" stroke-width="2.6"/>
            <circle cx="15" cy="19" r="1.5" fill="#d8121c" stroke="none"/>
          </svg>
        </li>
        <li aria-label="Headlights">
          <svg class="features__icon" width="34" height="28" viewBox="0 0 34 28" fill="none" stroke="#fff" stroke-width="2.4" stroke-linecap="round">
            <path d="M14 4 C6 4 4 9 4 14 C4 19 6 24 14 24 Z" fill="#fff"/>
            <path d="M19 7 H31 M19 12 H31 M19 17 H31 M19 22 H31"/>
          </svg>
        </li>
        <li aria-label="Horn">
          <svg class="features__icon" width="44" height="28" viewBox="0 0 44 28" fill="none" stroke="#fff" stroke-width="2" stroke-linecap="round">
            <path d="M8 14 L26 8 C30 6 34 4 36 4 V24 C34 24 30 22 26 20 L8 16 Z M12 15 V21 H18 V17"/>
            <path d="M2 8 L5 10 M1 14 H5 M2 20 L5 18"/>
          </svg>
        </li>
        <li aria-label="Turn signals">
          <svg class="features__icon" width="46" height="28" viewBox="0 0 46 28" fill="none" stroke="#fff" stroke-width="2.2" stroke-linejoin="round">
            <path d="M2 14 L12 4 V9 H20 V19 H12 V24 Z"/>
            <path d="M44 14 L34 4 V9 H26 V19 H34 V24 Z"/>
          </svg>
        </li>
        <li aria-label="Traffic legal lighting">
          <svg class="features__icon" width="24" height="28" viewBox="0 0 24 28" fill="#fff">
            <rect x="7" y="1" width="10" height="26" rx="2"/>
            <rect x="2" y="4" width="4" height="3"/><rect x="18" y="4" width="4" height="3"/>
            <rect x="2" y="12" width="4" height="3"/><rect x="18" y="12" width="4" height="3"/>
            <rect x="2" y="20" width="4" height="3"/><rect x="18" y="20" width="4" height="3"/>
            <circle cx="12" cy="6" r="2.4" fill="#d8121c"/>
            <circle cx="12" cy="14" r="2.4" fill="#d8121c"/>
            <circle cx="12" cy="22" r="2.4" fill="#d8121c"/>
          </svg>
        </li>
      </ul>
    </div>

    <div class="vehicle vehicle--utility" role="img" aria-label="Black utility side-by-side vehicle with cargo bed"></div>
  </div>
</body>
</html>
```